Business Card for a New Zealand IT Startup

I need a business card for VELTA Holdings. We are a young startup based in New Zealand working in internet marketing and web development. The design should have some element connected to New Zealand, such as wave, koru or silver fern, just don't use a kiwi bird.

```html
<!DOCTYPE html>
<html lang="en">
<head>
<meta charset="utf-8">
<title>VELTA Holdings – Business Card</title>
<link href="https://fonts.googleapis.com/css2?family=Open+Sans:wght@400;600;700;800&display=swap" rel="stylesheet">
<style>
  :root {
    --brand-blue: #0a6fc2;
    --brand-blue-soft: #1a7bca;
    --brand-blue-faint: rgba(255,255,255,.08);
    --brand-orange: #f05a22;
    --ink: #222428;
    --paper: #ffffff;
    --stage: #e6e7e9;
  }
  * { box-sizing: border-box; margin: 0; padding: 0; }
  html, body {
    width: 1200px; height: 782px; overflow: hidden;
    background: var(--stage);
    font-family: "Open Sans", Arial, sans-serif;
  }
  .sheet {
    width: 1200px; height: 782px;
    display: flex; align-items: center; justify-content: center; gap: 40px;
  }
  .card {
    position: relative;
    width: 540px; height: 308px;
    box-shadow: 0 6px 18px rgba(0,0,0,.18);
    overflow: hidden;
  }

  /* Front */
  .card-front { background: var(--paper); color: var(--ink); }
  .holder { position: absolute; left: 30px; top: 34px; }
  .holder-name {
    font-weight: 700; font-size: 17px; letter-spacing: .3px;
    color: var(--brand-blue); text-transform: uppercase;
  }
  .holder-role { font-size: 12px; margin-top: 1px; }

  .contact-list { position: absolute; left: 30px; top: 138px; list-style: none; }
  .contact-item {
    display: flex; align-items: center; gap: 6px;
    font-size: 13px; line-height: 19px;
  }
  .contact-icon { width: 11px; height: 11px; fill: var(--brand-blue); flex: none; }

  .brand-lockup {
    position: absolute; right: 44px; top: 112px;
    display: flex; align-items: center; gap: 9px;
  }
  .brand-name {
    font-weight: 800; font-size: 29px; color: var(--brand-blue);
    letter-spacing: .4px; line-height: 1;
  }
  .brand-dot { width: 18px; height: 18px; border-radius: 50%; background: var(--brand-orange); flex: none; }

  .address {
    position: absolute; right: 30px; top: 192px;
    text-align: right; font-size: 14px; line-height: 19px; font-style: normal;
  }
  .edge-waves { position: absolute; left: 0; bottom: 0; width: 540px; height: 56px; }

  /* Back */
  .card-back { background: var(--brand-blue); }
  .back-texture {
    position: absolute; inset: 0;
    background: linear-gradient(135deg, var(--brand-blue) 0%, var(--brand-blue-soft) 50%, var(--brand-blue) 100%);
  }
  .back-waves { position: absolute; left: 0; bottom: 0; width: 540px; height: 90px; }
  .back-lockup {
    position: absolute; left: 50%; top: 50%;
    transform: translate(-50%, -50%);
    display: flex; align-items: center; gap: 8px;
  }
  .back-name { font-weight: 800; font-size: 22px; color: var(--paper); letter-spacing: .5px; }
  .back-dot { width: 12px; height: 12px; border-radius: 50%; background: var(--brand-orange); }
</style>
</head>
<body>
<main class="sheet">

  <section class="card card-front">
    <div class="holder">
      <p class="holder-name">Daniel Harper</p>
      <p class="holder-role">Managing Director</p>
    </div>

    <ul class="contact-list">
      <li class="contact-item">
        <svg class="contact-icon" viewBox="0 0 12 12"><path d="M1 3.5C1 2 2 1 3.5 1h5C10 1 11 2 11 3.5V4H8.5V3h-5v1H1zM2 5h8l1 5H1z"/></svg>
        044-123 456 789
      </li>
      <li class="contact-item">
        <svg class="contact-icon" viewBox="0 0 12 12"><path d="M3.5 0h5A1 1 0 0 1 9.5 1v10a1 1 0 0 1-1 1h-5a1 1 0 0 1-1-1V1a1 1 0 0 1 1-1zM4 2v7h4V2z"/></svg>
        044-123 456 789
      </li>
      <li class="contact-item">
        <svg class="contact-icon" viewBox="0 0 12 12"><path d="M0 2h12v8H0zM1 3l5 3.5L11 3v-.2H1z" fill-rule="evenodd"/></svg>
        info@webname.com
      </li>
      <li class="contact-item">
        <svg class="contact-icon" viewBox="0 0 12 12"><circle cx="6" cy="6" r="5.5"/></svg>
        www.websitename.com
      </li>
    </ul>

    <div class="brand-lockup">
      <span class="brand-dot"></span>
      <span class="brand-name">VELTA Holdings</span>
    </div>

    <address class="address">
      12345, Address Goes Here<br>
      Country Name, 123456
    </address>

    <svg class="edge-waves" viewBox="0 0 540 56" aria-hidden="true">
      <path d="M0,20 C60,12 120,28 180,20 C210,16 235,16 252,20 L244,30 C225,26 205,26 180,30 C120,38 60,22 0,30 Z" fill="var(--brand-blue)"/>
      <path d="M262,22 C330,10 400,34 470,22 C500,17 522,17 540,20 L540,44 L244,44 Z" fill="var(--brand-orange)"/>
    </svg>
  </section>

  <section class="card card-back">
    <div class="back-texture" role="img" aria-label="Faint repeated brand pattern across the blue card back"></div>
    <svg class="back-waves" viewBox="0 0 540 90" aria-hidden="true">
      <path d="M0,40 C90,20 180,60 270,40 C360,20 450,60 540,40 L540,90 L0,90 Z" fill="var(--brand-blue-faint)"/>
      <path d="M0,62 C90,44 180,80 270,62 C360,44 450,80 540,62 L540,90 L0,90 Z" fill="var(--brand-blue-faint)"/>
    </svg>
    <div class="back-lockup">
      <span class="back-dot"></span>
      <span class="back-name">VELTA Holdings</span>
    </div>
  </section>

</main>
</body>
</html>
```